Create a memorable Stationary for Security Software Company

Velbrantix is the worldwide leader in securing the Internet. Making Internet communications and critical data secure, reliable and available everywhere has been and continues to be our ongoing vision. We are committed to staying focused on real customer needs and to developing new and innovative security solutions that redefine the security landscape.

Industry/Entity Type

Internet

Font styles to use
Serif
Sans Serif
Script

Colors
0792cd
33a6d7
85cae6

```html
<!DOCTYPE html>
<html lang="en">
<head>
<meta charset="utf-8">
<title>Velbrantix Business Card</title>
<link href="https://fonts.googleapis.com/css2?family=Open+Sans:wght@400;600&display=swap" rel="stylesheet">
<style>
  :root {
    --brand-deep: #0792cd;
    --brand-mid: #33a6d7;
    --brand-light: #85cae6;
    --ink: #3a3a3a;
    --ink-soft: #555555;
    --paper: #ffffff;
    --stage: #ece7e0;
    --edge: #6f6f6f;
  }
  * { margin: 0; padding: 0; box-sizing: border-box; }
  html, body { width: 1200px; height: 1117px; overflow: hidden; }
  body {
    background: var(--stage);
    font-family: "Open Sans", Arial, sans-serif;
    position: relative;
  }
  .card {
    position: absolute;
    border-radius: 36px;
    overflow: hidden;
  }
  .card-front {
    left: 45px; top: 64px; width: 817px; height: 468px;
    background: var(--paper);
    border: 1.5px solid #9a9a9a;
  }
  .card-back {
    left: 330px; top: 581px; width: 818px; height: 466px;
    background: var(--brand-light);
    border: 1.5px solid var(--edge);
  }
  .front-wave { position: absolute; left: 0; top: 0; width: 817px; height: 468px; }
  .brand-mark {
    position: absolute;
    display: flex; align-items: center; gap: 14px;
  }
  .brand-mark .dot {
    width: 34px; height: 34px; border-radius: 50%;
    background: var(--brand-mid);
  }
  .brand-mark .brand-name {
    font-weight: 600; color: var(--brand-mid); font-size: 50px; line-height: 1;
  }
  .card-front .brand-mark { left: 60px; top: 145px; }
  .card-back .brand-mark { left: 50%; top: 150px; transform: translateX(-50%); }
  .card-back .brand-mark .brand-name { color: var(--brand-deep); font-size: 58px; }
  .card-back .brand-mark .dot { background: var(--brand-deep); width: 40px; height: 40px; }
  .divider {
    position: absolute; left: 452px; top: 62px; width: 1.5px; height: 221px;
    background: #b9b9b9;
  }
  .contact { position: absolute; left: 487px; top: 62px; }
  .person-name { color: var(--brand-deep); font-weight: 600; font-size: 26px; line-height: 34px; }
  .person-title { color: var(--ink-soft); font-size: 23px; line-height: 32px; margin-bottom: 10px; }
  .contact-line {
    display: flex; align-items: center; gap: 9px;
    color: var(--ink); font-size: 20px; line-height: 34px;
  }
  .contact-line svg { width: 18px; height: 18px; fill: var(--brand-deep); flex: none; }
  .address {
    position: absolute; right: 25px; bottom: 14px;
    color: var(--paper); font-size: 19px; line-height: 28px; text-align: right;
  }
  .back-url {
    position: absolute; left: 0; right: 0; top: 358px;
    text-align: center; color: var(--ink); font-size: 25px; letter-spacing: 5px;
  }
</style>
</head>
<body>
  <section class="card card-front" aria-label="Business card front">
    <svg class="front-wave" viewBox="0 0 817 468" aria-hidden="true">
      <path d="M0 290 C 150 395, 260 430, 360 426 C 470 420, 560 350, 817 310 L817 468 L0 468 Z" fill="var(--brand-light)"/>
      <path d="M0 304 C 150 408, 260 438, 360 433 C 470 426, 560 358, 817 322" fill="none" stroke="var(--paper)" stroke-width="5"/>
      <path d="M0 318 C 150 420, 260 445, 360 440 C 470 432, 560 370, 817 335 L817 468 L0 468 Z" fill="var(--brand-deep)"/>
    </svg>
    <div class="brand-mark">
      <span class="dot"></span>
      <span class="brand-name">Velbrantix</span>
    </div>
    <div class="divider"></div>
    <div class="contact">
      <p class="person-name">Your Name</p>
      <p class="person-title">Title</p>
      <p class="contact-line">
        <svg viewBox="0 0 24 24"><path d="M6.6 10.8a15.1 15.1 0 0 0 6.6 6.6l2.2-2.2c.3-.3.7-.4 1-.2 1.1.4 2.3.6 3.6.6.6 0 1 .4 1 1V20c0 .6-.4 1-1 1A17 17 0 0 1 3 4c0-.6.4-1 1-1h3.5c.6 0 1 .4 1 1 0 1.3.2 2.5.6 3.6.1.3 0 .7-.2 1z"/></svg>
        012-345-6789
      </p>
      <p class="contact-line">
        <svg viewBox="0 0 24 24"><path d="M7 1h10a2 2 0 0 1 2 2v18a2 2 0 0 1-2 2H7a2 2 0 0 1-2-2V3a2 2 0 0 1 2-2zm0 3v10h10V4zm3 14v2h4v-2z"/></svg>
        012-345-6789
      </p>
      <p class="contact-line">
        <svg viewBox="0 0 24 24"><path d="M2 5h20v14H2zm2 2v.5l8 5.5 8-5.5V7zm0 2.9V17h16V9.9l-8 5.5z"/></svg>
        info@velbrantix.com.com
      </p>
      <p class="contact-line">
        <svg viewBox="0 0 24 24"><path d="M12 2a10 10 0 1 0 0 20 10 10 0 0 0 0-20zm6.9 6h-3a15 15 0 0 0-1.3-4A8 8 0 0 1 18.9 8zM12 4c.8 1.2 1.5 2.5 1.9 4h-3.8c.4-1.5 1.1-2.8 1.900-4zM4.3 14a8 8 0 0 1 0-4h3.4a16 16 0 0 0 0 4zm.8 2h3a15 15 0 0 0 1.3 4A8 8 0 0 1 5.1 16zm3-8h-3a8 8 0 0 1 4.3-4 15 15 0 0 0-1.3 4zM12 20c-.8-1.2-1.5-2.5-1.9-4h3.8c-.4 1.5-1.1 2.8-1.9 4zm2.3-6H9.7a14 14 0 0 1 0-4h4.6a14 14 0 0 1 0 4zm.3 6a15 15 0 0 0 1.3-4h3a8 8 0 0 1-4.3 4zm1.7-6a16 16 0 0 0 0-4h3.4a8 8 0 0 1 0 4z"/></svg>
        www.velbrantix.com.com
      </p>
    </div>
    <p class="address">Street Name, City Name<br>Zipcode-012345</p>
  </section>

  <section class="card card-back" aria-label="Business card back">
    <div class="brand-mark">
      <span class="dot"></span>
      <span class="brand-name">Velbrantix</span>
    </div>
    <p class="back-url">www.velbrantix.com.com</p>
  </section>
</body>
</html>
```